New Innovative Counselling and psychotherapy Service needs Business Card design

Keep it simple and professional. On one side, just company name and logo (perhaps in all blue) and maybe a tag line.

On other side (all white) my name and Qualifications in centre

Industry/Entity Type

Health And Wellness

Contact Information for Business Card

Dara Whelby
Counsellor & Psychotherapist
BSc (Psychol.), BA, Dip. (Couns. & Psych.), PG.Cert (CBT), FGTrK, ONRE

I will also require Mobile no, Email and web site address of which I'll pass on to final designer.

Font styles to use
Sans Serif

Requirements
Must have
• My Logo Only and please use the colours in logo that is in it.
Should not have
• Any other images

```html
<!DOCTYPE html>
<html lang="en">
<head>
<meta charset="utf-8">
<title>Tidewell Path – Business Card</title>
<link rel="stylesheet" href="https://fonts.googleapis.com/css2?family=Lato:ital,wght@0,400;0,700;1,400&display=swap">
<style>
  :root {
    --stage: #333333;
    --card-white: #ffffff;
    --brand-blue: #45b3ec;
    --brand-green: #8dc63f;
    --ink: #2b2b2b;
    --ink-soft: #3a3a3a;
    --rule: #d6d6d6;
    --rule-light: rgba(255,255,255,0.35);
  }
  * { margin: 0; padding: 0; box-sizing: border-box; }
  html, body { width: 1200px; height: 900px; overflow: hidden; }
  body { background: var(--stage); font-family: "Lato", Arial, sans-serif; position: relative; }

  .card {
    position: absolute;
    width: 477px;
    height: 293px;
    box-shadow: 3px 4px 6px rgba(0,0,0,0.55);
  }
  .card--front {
    left: 120px; top: 275px;
    background: var(--card-white);
    border-radius: 0 52px 0 52px;
  }
  .card--back {
    left: 606px; top: 274px;
    background: var(--brand-blue);
    border-radius: 52px 0 52px 0;
  }

  .brand { position: absolute; display: flex; align-items: center; }
  .brand__dot { border-radius: 50%; flex: none; }
  .brand__name { font-weight: 400; white-space: nowrap; letter-spacing: 0.2px; }

  .card--front .brand { left: 177px; top: 71px; }
  .card--front .brand__dot { width: 52px; height: 52px; background: var(--brand-blue); margin-right: 21px; }
  .card--front .brand__name { font-size: 27px; color: var(--ink); }

  .card--back .brand { left: 66px; top: 107px; }
  .card--back .brand__dot { width: 68px; height: 68px; background: var(--card-white); margin-right: 25px; }
  .card--back .brand__name { font-size: 34px; color: var(--card-white); }

  .person { position: absolute; left: 30px; top: 173px; }
  .person__name { font-size: 17px; letter-spacing: 0.3px; line-height: 20px; }
  .person__first { color: var(--brand-blue); }
  .person__last { color: var(--brand-green); }
  .person__role { font-size: 13px; color: var(--ink-soft); line-height: 17px; }
  .person__rule {
    position: absolute; left: 223px; top: 200px;
    width: 224px; height: 1px; background: var(--rule);
  }
  .qualifications {
    position: absolute; left: 30px; top: 214px;
    font-size: 13px; font-style: italic; color: var(--ink-soft); line-height: 17.5px;
  }

  .contact {
    position: absolute; right: 26px; top: 217px;
    list-style: none; text-align: right;
    font-size: 14px; color: var(--ink); line-height: 17.5px;
  }
  .contact__item { display: flex; justify-content: flex-end; align-items: center; }
  .contact__icon { width: 10px; height: 10px; margin-left: 1px; flex: none; }

  .back__rule {
    position: absolute; left: 69px; top: 211px;
    width: 340px; height: 1px; background: var(--rule-light);
  }
  .tagline {
    position: absolute; left: 0; right: 0; top: 231px;
    text-align: center; color: var(--card-white);
    font-size: 10.5px; font-weight: 700; text-transform: uppercase; letter-spacing: 0.1px;
  }
</style>
</head>
<body>

<section class="card card--front" aria-label="Business card front">
  <div class="brand">
    <span class="brand__dot"></span>
    <span class="brand__name">Tidewell Path</span>
  </div>

  <div class="person">
    <p class="person__name"><span class="person__first">DARA</span> <span class="person__last">WHELBY</span></p>
    <p class="person__role">Counsellor &amp; Psychotherapist</p>
  </div>
  <span class="person__rule"></span>

  <p class="qualifications">BSc (Psychol.), BA,<br>Dip. (Couns. &amp; Psych.),<br>PG.Cert (CBT), FGTrK, ONRE</p>

  <ul class="contact">
    <li class="contact__item">087 5302 916
      <svg class="contact__icon" viewBox="0 0 10 10" aria-hidden="true">
        <path d="M1 3.5 Q5 0.5 9 3.5 L8 5 L6.5 4.2 L6.5 3.4 Q5 3 3.5 3.4 L3.5 4.2 L2 5 Z" fill="var(--brand-blue)"/>
        <rect x="2.5" y="5.5" width="5" height="3" rx="0.8" fill="var(--brand-blue)"/>
      </svg>
    </li>
    <li class="contact__item">info@tidewellpath.com
      <svg class="contact__icon" viewBox="0 0 10 10" aria-hidden="true">
        <rect x="0.5" y="2" width="9" height="6.5" rx="0.8" fill="var(--brand-blue)"/>
        <path d="M1 2.6 L5 5.8 L9 2.6" fill="none" stroke="#fff" stroke-width="0.9"/>
      </svg>
    </li>
    <li class="contact__item">www.tidewellpath.com
      <svg class="contact__icon" viewBox="0 0 10 10" aria-hidden="true">
        <circle cx="5" cy="5" r="4.5" fill="var(--brand-blue)"/>
        <ellipse cx="5" cy="5" rx="1.8" ry="4.3" fill="none" stroke="#fff" stroke-width="0.7"/>
        <line x1="0.6" y1="5" x2="9.4" y2="5" stroke="#fff" stroke-width="0.7"/>
      </svg>
    </li>
  </ul>
</section>

<section class="card card--back" aria-label="Business card back">
  <div class="brand">
    <span class="brand__dot"></span>
    <span class="brand__name">Tidewell Path</span>
  </div>
  <span class="back__rule"></span>
  <p class="tagline">Caring for your &nbsp;psychological well-being is our top priority</p>
</section>

</body>
</html>
```